Podiatry clinic requires a modern revamp and editing of existing website.

I would like a fresh new look and updated information for my current business website. An easy to navigate site with prominent address and phone number for call to action. We are a podiatry clinic that focuses on general and sports podiatry.
I would like 4 pages; including Home page, About Us, Services & Contact.
www.brambleridgepodiatry.net

Target Market(s)

Active working professionals.

Industry/Entity Type

Medical

Coding

Coded - Design and coding required

Number of Pages Required

4 page

Font styles to use
Sans Serif

Colors
6b449b

Requirements
Must have
• A modern look with logo and active images; clean and uncluttered. Visible phone number and address for call to action.
• 4 pages - Home, About Us, Services, Contact.
• Home page - update address & service logos.
• About Us - update of personal information.
• Services - Revamp of existing page.
• Contact page to include Google map, email & phone number.
Nice to have
• Ability to add content easily; eg. a blog or adding video onto Home page.
• Link to Facebook page.

```html
<!DOCTYPE html>
<html lang="en">
<head>
<meta charset="utf-8">
<title>Bramble Ridge Podiatry</title>
<link href="https://fonts.googleapis.com/css2?family=Lato:wght@400;700&family=Questrial&display=swap" rel="stylesheet">
<style>
:root{
  --purple:#4a3596;
  --purple-mid:#5a46a0;
  --purple-text:#3e2f8f;
  --orange:#ef7a2a;
  --green:#7dc242;
  --ink:#333;
  --white:#fff;
}
*{margin:0;padding:0;box-sizing:border-box}
html,body{width:892px;height:1200px;overflow:hidden}
body{font-family:'Lato',sans-serif;color:var(--ink);background:var(--white);position:relative}
.heading{font-family:'Questrial',sans-serif}
.abs{position:absolute}

.topbar{left:0;top:0;width:892px;height:22px;background:var(--purple);color:var(--white);font-size:10px}
.social{left:426px;top:6px;display:flex;gap:14px}
.social span{width:9px;height:9px;border-radius:50%;background:rgba(255,255,255,.85);display:block}
.top-contact{top:0;height:22px;display:flex;align-items:center}
.top-contact .icon{width:22px;height:22px;background:var(--green);display:flex;align-items:center;justify-content:center}
.top-contact .txt{padding:0 0 0 8px}

.header{left:0;top:22px;width:892px;height:79px;background:var(--white);border-bottom:1px solid #ddd}
.brand{left:74px;top:28px;display:flex;align-items:center;gap:8px;font-family:'Questrial',sans-serif;font-size:17px;color:var(--purple-text);font-weight:400}
.brand .dot{width:16px;height:16px;border-radius:50%;background:var(--orange)}
.nav a{position:absolute;font-size:10.5px;color:var(--purple-text);text-decoration:none;top:34px}
.nav .active{left:373px;top:24px;width:64px;height:31px;border:1px solid var(--purple-text);display:flex;align-items:center;justify-content:center;font-weight:700}
.book{left:670px;top:24px;width:149px;height:31px;background:var(--green);color:var(--white);font-family:'Questrial',sans-serif;font-size:12px;font-weight:700;display:flex;align-items:center;justify-content:center;gap:6px}

.hero{left:0;top:101px;width:892px;height:350px;background:linear-gradient(180deg,#8a9aa3 0%,#5d6469 55%,#2d2f31 100%)}
.hero .arrow{top:165px;width:21px;height:21px;border:1px solid var(--white);display:flex;align-items:center;justify-content:center}
.hero .caption{left:0;width:892px;top:310px;text-align:center;color:var(--white);font-size:23px;font-weight:700;font-family:'Questrial',sans-serif;text-shadow:0 1px 3px rgba(0,0,0,.5)}

.welcome{left:0;top:478px;width:892px;text-align:center}
.welcome h1{font-size:27px;font-weight:400;color:var(--orange)}
.welcome h1 strong{color:var(--purple-text);font-weight:700}
.welcome .rule{left:206px;top:49px;width:480px;height:1px;background:#ccc}
.welcome p{position:absolute;left:120px;top:68px;width:652px;font-size:10px;line-height:18.4px;color:#333}

.services{left:0;top:689px;width:892px;height:295px;background:linear-gradient(135deg,#e8762e 0%,#f08a3a 50%,#e06a22 100%);color:var(--white)}
.services h2{position:absolute;left:0;width:892px;top:30px;text-align:center;font-size:26px;font-weight:400}
.services h2 strong{font-weight:700}
.services .rule{left:331px;top:65px;width:230px;height:1px;background:rgba(255,255,255,.8)}
.services .divider{left:458px;top:93px;width:1px;height:126px;background:rgba(255,255,255,.4)}
.services h3{position:absolute;font-size:15px;font-weight:700;text-decoration:underline;top:89px}
.item{position:absolute;display:flex;align-items:center;gap:7px;font-size:11.5px}
.readmore{left:406px;top:243px;width:74px;height:25px;background:var(--purple-text);font-size:10.5px;font-weight:700;display:flex;align-items:center;justify-content:center}

.footer{left:0;top:984px;width:892px;height:186px;background:var(--purple-mid);color:var(--white)}
.footer h4{position:absolute;top:38px;font-family:'Questrial',sans-serif;font-size:12px;font-weight:700}
.footer .underline{position:absolute;top:58px;height:1px;background:rgba(255,255,255,.25)}
.footer .vsep{top:25px;width:1px;height:140px;background:rgba(255,255,255,.15)}
.links{position:absolute;left:74px;top:64px;width:88px;list-style:none;font-size:8.5px}
.links li{height:25px;display:flex;align-items:center;gap:6px;border-bottom:1px solid rgba(255,255,255,.15)}
.links li:last-child{border-bottom:none}
.contact-list{position:absolute;left:238px;top:64px;width:136px;font-size:8.5px;line-height:13px}
.contact-list div{display:flex;gap:8px;padding:4px 0 6px;border-bottom:1px solid rgba(255,255,255,.15)}
.contact-list div:last-child{border-bottom:none}
.map{left:461px;top:70px;width:167px;height:82px;background:linear-gradient(135deg,#e9e4d8,#d5d9cf 60%,#c9d6d0)}
.faint-brand{left:704px;top:88px;font-family:'Questrial',sans-serif;font-size:15px;color:rgba(255,255,255,.35);display:flex;align-items:center;gap:6px}
.faint-brand .dot{width:13px;height:13px;border-radius:50%;background:rgba(255,255,255,.3)}

.copyright{left:0;top:1170px;width:892px;height:30px;background:var(--green);color:#333;font-size:10px;display:flex;align-items:center;justify-content:center}
.copyright strong{margin:0 2px}
</style>
</head>
<body>

<div class="abs topbar">
  <div class="abs social"><span></span><span></span><span></span><span></span></div>
  <div class="abs top-contact" style="left:535px">
    <div class="icon"><svg width="10" height="10" viewBox="0 0 24 24"><path fill="#fff" d="M6.6 10.8a15 15 0 006.6 6.6l2.2-2.2a1 1 0 011-.25 11 11 0 003.6.6 1 1 0 011 1V20a1 1 0 01-1 1A17 17 0 013 4a1 1 0 011-1h3.5a1 1 0 011 1 11 11 0 00.6 3.6 1 1 0 01-.25 1z"/></svg></div>
    <span class="txt">415-207-3391</span>
  </div>
  <div class="abs top-contact" style="left:646px">
    <div class="icon"><svg width="10" height="8" viewBox="0 0 20 14"><path fill="#fff" d="M0 0h20v2l-10 6L0 2zM0 4l10 6 10-6v10H0z"/></svg></div>
    <span class="txt">hello@brambleridgepodiatry.net</span>
  </div>
</div>

<header class="abs header">
  <div class="abs brand"><span class="dot"></span>Bramble Ridge Podiatry</div>
  <nav class="nav">
    <a class="active" href="#">Home</a>
    <a href="#" style="left:452px">About Us</a>
    <a href="#" style="left:528px">Services</a>
    <a href="#" style="left:601px">Contact</a>
  </nav>
  <div class="abs book">
    <svg width="14" height="14" viewBox="0 0 16 16"><circle cx="7" cy="4" r="3" fill="#fff"/><path d="M2 15c0-4 2-6 5-6s5 2 5 6z" fill="#fff"/></svg>
    Book Appointment
  </div>
</header>

<section class="abs hero" role="img" aria-label="Photo of runners' feet on a treadmill with a glowing foot bone highlight">
  <div class="abs arrow" style="left:44px"><svg width="10" height="8" viewBox="0 0 10 8"><path d="M10 4H2M4 1L1 4l3 3" stroke="#fff" stroke-width="1.4" fill="none"/></svg></div>
  <div class="abs arrow" style="left:827px"><svg width="10" height="8" viewBox="0 0 10 8"><path d="M0 4h8M6 1l3 3-3 3" stroke="#fff" stroke-width="1.4" fill="none"/></svg></div>
  <div class="abs caption">Bramble Ridge Podiatry is a Podiatry clinic in the heart of Fernvale</div>
</section>

<section class="abs welcome">
  <h1 class="heading">Welcome to <strong>Bramble Ridge Podiatry</strong></h1>
  <div class="abs rule"></div>
  <p>Bramble Ridge Podiatry is a Podiatry clinic in the heart of Fernvale CBD. We are located between Ashby &amp; Reed Streets in the Harlow Business Centre / Linden Court Complex.<br>Our podiatrists are fully qualified health professionals who are able to diagnose, treat, manage or help to prevent all medical conditions that affect the feet and lower limb.<br>We provide General Podiatry Treatment and some Specialised Services in relation to various foot conditions, including Sports Injuries, Orthotic Therapy and Nail Surgery.</p>
</section>

<section class="abs services" role="img" aria-label="Orange-tinted photo of a runner's shoe on an autumn path">
  <h2 class="heading">Our <strong>Services</strong></h2>
  <div class="abs rule"></div>
  <div class="abs divider"></div>
  <h3 class="heading" style="left:180px">General Treatments</h3>
  <h3 class="heading" style="left:540px">Specialised Treatments</h3>

  <div class="item" style="left:104px;top:128px"><svg width="13" height="13" viewBox="0 0 14 14"><path d="M11 7v6H1V3h7" stroke="#fff" stroke-width="1.6" fill="none"/><path d="M4 6l3 3 6-7" stroke="#fff" stroke-width="1.8" fill="none"/></svg>Nails</div>
  <div class="item" style="left:206px;top:128px"><svg width="13" height="13" viewBox="0 0 14 14"><path d="M11 7v6H1V3h7" stroke="#fff" stroke-width="1.6" fill="none"/><path d="M4 6l3 3 6-7" stroke="#fff" stroke-width="1.8" fill="none"/></svg>Corns</div>
  <div class="item" style="left:332px;top:128px"><svg width="13" height="13" viewBox="0 0 14 14"><path d="M11 7v6H1V3h7" stroke="#fff" stroke-width="1.6" fill="none"/><path d="M4 6l3 3 6-7" stroke="#fff" stroke-width="1.8" fill="none"/></svg>Callus</div>
  <div class="item" style="left:104px;top:163px"><svg width="13" height="13" viewBox="0 0 14 14"><path d="M11 7v6H1V3h7" stroke="#fff" stroke-width="1.6" fill="none"/><path d="M4 6l3 3 6-7" stroke="#fff" stroke-width="1.8" fill="none"/></svg>Warts</div>
  <div class="item" style="left:206px;top:163px"><svg width="13" height="13" viewBox="0 0 14 14"><path d="M11 7v6H1V3h7" stroke="#fff" stroke-width="1.6" fill="none"/><path d="M4 6l3 3 6-7" stroke="#fff" stroke-width="1.8" fill="none"/></svg>Skin Disorders</div>
  <div class="item" style="left:332px;top:163px"><svg width="13" height="13" viewBox="0 0 14 14"><path d="M11 7v6H1V3h7" stroke="#fff" stroke-width="1.6" fill="none"/><path d="M4 6l3 3 6-7" stroke="#fff" stroke-width="1.8" fill="none"/></svg>Heel Pain</div>
  <div class="item" style="left:104px;top:198px"><svg width="13" height="13" viewBox="0 0 14 14"><path d="M11 7v6H1V3h7" stroke="#fff" stroke-width="1.6" fill="none"/><path d="M4 6l3 3 6-7" stroke="#fff" stroke-width="1.8" fill="none"/></svg>Knee Pain</div>
  <div class="item" style="left:206px;top:198px"><svg width="13" height="13" viewBox="0 0 14 14"><path d="M11 7v6H1V3h7" stroke="#fff" stroke-width="1.6" fill="none"/><path d="M4 6l3 3 6-7" stroke="#fff" stroke-width="1.8" fill="none"/></svg>Toe Deformities</div>

  <div class="item" style="left:520px;top:128px"><svg width="13" height="13" viewBox="0 0 14 14"><path d="M11 7v6H1V3h7" stroke="#fff" stroke-width="1.6" fill="none"/><path d="M4 6l3 3 6-7" stroke="#fff" stroke-width="1.8" fill="none"/></svg>Diabetic Management</div>
  <div class="item" style="left:697px;top:128px"><svg width="13" height="13" viewBox="0 0 14 14"><path d="M11 7v6H1V3h7" stroke="#fff" stroke-width="1.6" fill="none"/><path d="M4 6l3 3 6-7" stroke="#fff" stroke-width="1.8" fill="none"/></svg>Nail Surgery</div>
  <div class="item" style="left:520px;top:163px"><svg width="13" height="13" viewBox="0 0 14 14"><path d="M11 7v6H1V3h7" stroke="#fff" stroke-width="1.6" fill="none"/><path d="M4 6l3 3 6-7" stroke="#fff" stroke-width="1.8" fill="none"/></svg>Gait Analysis</div>
  <div class="item" style="left:697px;top:163px"><svg width="13" height="13" viewBox="0 0 14 14"><path d="M11 7v6H1V3h7" stroke="#fff" stroke-width="1.6" fill="none"/><path d="M4 6l3 3 6-7" stroke="#fff" stroke-width="1.8" fill="none"/></svg>Orthotic Therapy</div>
  <div class="item" style="left:520px;top:198px"><svg width="13" height="13" viewBox="0 0 14 14"><path d="M11 7v6H1V3h7" stroke="#fff" stroke-width="1.6" fill="none"/><path d="M4 6l3 3 6-7" stroke="#fff" stroke-width="1.8" fill="none"/></svg>Biomechanical Assessment</div>

  <div class="abs readmore">Read More</div>
</section>

<footer class="abs footer">
  <div class="abs vsep" style="left:202px"></div>
  <div class="abs vsep" style="left:424px"></div>
  <div class="abs vsep" style="left:670px"></div>

  <h4 style="left:74px">Quick Links</h4>
  <div class="underline" style="left:74px;width:88px"></div>
  <ul class="links">
    <li><svg width="4" height="6" viewBox="0 0 4 6"><path d="M0 0l4 3-4 3z" fill="#fff"/></svg>Home</li>
    <li><svg width="4" height="6" viewBox="0 0 4 6"><path d="M0 0l4 3-4 3z" fill="#fff"/></svg>About Us</li>
    <li><svg width="4" height="6" viewBox="0 0 4 6"><path d="M0 0l4 3-4 3z" fill="#fff"/></svg>Services</li>
    <li><svg width="4" height="6" viewBox="0 0 4 6"><path d="M0 0l4 3-4 3z" fill="#fff"/></svg>Contact</li>
  </ul>

  <h4 style="left:238px">Contact Details</h4>
  <div class="underline" style="left:238px;width:136px"></div>
  <div class="contact-list">
    <div><svg width="7" height="10" viewBox="0 0 10 14"><path d="M5 0a5 5 0 015 5c0 4-5 9-5 9S0 9 0 5a5 5 0 015-5z" fill="#fff"/><circle cx="5" cy="5" r="2" fill="#5a46a0"/></svg><span>Suite 204 / 118 Harlow Lane<br>Fernvale 4120</span></div>
    <div><svg width="8" height="8" viewBox="0 0 24 24"><path fill="#fff" d="M6.6 10.8a15 15 0 006.6 6.6l2.2-2.2a1 1 0 011-.25 11 11 0 003.6.6 1 1 0 011 1V20a1 1 0 01-1 1A17 17 0 013 4a1 1 0 011-1h3.5a1 1 0 011 1 11 11 0 00.6 3.6 1 1 0 01-.25 1z"/></svg><span>1300 482 905</span></div>
    <div><svg width="8" height="7" viewBox="0 0 20 14"><path fill="#fff" d="M0 0h20v2l-10 6L0 2zM0 4l10 6 10-6v10H0z"/></svg><span>info@brambleridgepodiatry.net</span></div>
  </div>

  <h4 style="left:461px">Location Map</h4>
  <div class="underline" style="left:461px;width:167px"></div>
  <div class="abs map" role="img" aria-label="Street map showing the clinic location"></div>

  <div class="abs faint-brand"><span class="dot"></span>Bramble Ridge Podiatry</div>
</footer>

<div class="abs copyright">Copyright © 2016&nbsp;<strong>Bramble Ridge Podiatry</strong>. All Rights Reserved.</div>

</body>
</html>
```